Pinecroft Ridge A4 Potrait foldout brochure

We need a brochure design for this residential land development. I have attached the a style that we like to base our design on. Full colour required. will provide files required for design also. PLEASE DO NOT COPY THIS DESIGN. Come up with a new style that gives you this feeling. Please note the plan needs to be positioned landscape on the inside 2 A4 Pages.

Industry/Entity Type

Residential

Font styles to use
Other font styles liked:
• Try with Century Gothich

Requirements
Must have
• use same colours as supplied in Pinecroft ridge brochure.
Nice to have
• nice modern simple background graphics

```html
<!DOCTYPE html>
<html lang="en">
<head>
<meta charset="utf-8">
<title>Pinecroft Ridge – Brochure Cover</title>
<link rel="stylesheet" href="https://fonts.googleapis.com/css2?family=Questrial&family=Lato:wght@400;700&display=swap">
<style>
  :root {
    --pink: #d77fb8;
    --lilac: #a98cc8;
    --violet: #6d5f9e;
    --slate: #5a6590;
    --teal: #6cc3c4;
    --navy: #2e3566;
    --frame: rgba(255, 255, 255, 0.22);
    --frame-line: rgba(255, 255, 255, 0.35);
    --brand: #0e5226;
    --ink: #ffffff;
    --fold: rgba(40, 40, 80, 0.25);
  }
  html, body {
    margin: 0;
    padding: 0;
    width: 1200px;
    height: 866px;
    overflow: hidden;
    background: #f2f2f2;
  }
  .spread {
    position: relative;
    width: 1200px;
    height: 866px;
    overflow: hidden;
  }
  .spread__background {
    position: absolute;
    inset: 0;
    background:
      radial-gradient(ellipse 420px 300px at 78% 60%, rgba(108, 195, 196, 0.55), transparent 70%),
      radial-gradient(ellipse 380px 320px at 30% 40%, rgba(215, 127, 184, 0.55), transparent 70%),
      radial-gradient(ellipse 300px 260px at 10% 85%, rgba(46, 53, 102, 0.55), transparent 70%),
      radial-gradient(ellipse 320px 260px at 95% 90%, rgba(46, 53, 102, 0.6), transparent 70%),
      linear-gradient(135deg, var(--lilac) 0%, var(--pink) 35%, var(--violet) 60%, var(--slate) 80%, var(--navy) 100%);
  }
  .spread__fold {
    position: absolute;
    left: 599px;
    top: 0;
    width: 2px;
    height: 866px;
    background: var(--fold);
  }
  .panel {
    position: absolute;
    top: 0;
    width: 600px;
    height: 866px;
  }
  .panel--back { left: 0; }
  .panel--front { left: 600px; }
  .panel__frame {
    position: absolute;
    top: 23px;
    width: 556px;
    height: 822px;
    background: var(--frame);
    border: 1px solid var(--frame-line);
    box-sizing: border-box;
  }
  .panel--back .panel__frame { left: 22px; }
  .panel--front .panel__frame { left: 22px; width: 558px; }

  .brand {
    position: absolute;
    left: 0;
    right: 0;
    text-align: center;
    font-family: "Questrial", "Century Gothic", sans-serif;
    color: var(--brand);
    white-space: nowrap;
  }
  .brand__mark {
    display: block;
    margin: 0 auto;
    border-radius: 50%;
    background: var(--brand);
  }
  .panel--front .brand { top: 150px; left: 20px; }
  .panel--front .brand__mark { width: 70px; height: 70px; margin-bottom: 34px; }
  .panel--front .brand__name { font-size: 56px; letter-spacing: 0.5px; }
  .panel--back .brand { top: 560px; }
  .panel--back .brand__mark { width: 36px; height: 36px; margin-bottom: 14px; }
  .panel--back .brand__name { font-size: 30px; }

  .contact {
    position: absolute;
    left: 0;
    right: 0;
    top: 674px;
    text-align: center;
    font-family: "Lato", sans-serif;
    color: var(--ink);
    font-size: 16px;
    line-height: 21px;
    text-shadow: 0 1px 2px rgba(0, 0, 0, 0.35);
    margin: 0;
    font-style: normal;
  }
  .contact__line { display: block; }
  .contact__line svg {
    width: 13px;
    height: 13px;
    vertical-align: -1px;
    margin-right: 4px;
    fill: var(--ink);
  }
  .contact__phone {
    font-weight: 700;
    font-size: 20px;
    margin: 6px 0 5px;
  }
  .contact__phone svg { width: 17px; height: 17px; vertical-align: -2px; }
  .contact__web { margin-top: 3px; }

  .front-url {
    position: absolute;
    left: 20px;
    right: 0;
    top: 794px;
    text-align: center;
    font-family: "Lato", sans-serif;
    font-size: 23px;
    color: var(--ink);
    text-shadow: 0 1px 2px rgba(0, 0, 0, 0.35);
  }
</style>
</head>
<body>
<main class="spread">
  <div class="spread__background" role="img" aria-label="Soft geometric pattern of overlapping triangles in pink, lilac, violet, teal and navy"></div>

  <section class="panel panel--back">
    <div class="panel__frame"></div>
    <div class="brand">
      <span class="brand__mark"></span>
      <span class="brand__name">Pinecroft Ridge</span>
    </div>
    <address class="contact">
      <span class="contact__line">
        <svg viewBox="0 0 24 24" aria-hidden="true"><path d="M12 2a7 7 0 0 0-7 7c0 5 7 13 7 13s7-8 7-13a7 7 0 0 0-7-7zm0 9.5A2.5 2.5 0 1 1 12 6.5a2.5 2.5 0 0 1 0 5z"/></svg>Pinecroft Ridge
      </span>
      <span class="contact__line">Larkspur Avenue 42b</span>
      <span class="contact__line">20817 City, State</span>
      <span class="contact__line contact__phone">
        <svg viewBox="0 0 24 24" aria-hidden="true"><path d="M6.6 10.8a15 15 0 0 0 6.6 6.6l2.2-2.2a1 1 0 0 1 1-.25 11.4 11.4 0 0 0 3.6.57 1 1 0 0 1 1 1V20a1 1 0 0 1-1 1A17 17 0 0 1 3 4a1 1 0 0 1 1-1h3.5a1 1 0 0 1 1 1c0 1.25.2 2.45.57 3.6a1 1 0 0 1-.25 1z"/></svg>+01 98 7654321
      </span>
      <span class="contact__line">
        <svg viewBox="0 0 24 24" aria-hidden="true"><path d="M2 5h20v14H2zm2 2v.5l8 5 8-5V7zm0 2.8V17h16V9.8l-8 5z"/></svg>info@pinecroftridge.com
      </span>
      <span class="contact__line contact__web">
        <svg viewBox="0 0 24 24" aria-hidden="true"><path d="M12 2a10 10 0 1 0 0 20 10 10 0 0 0 0-20zm6.9 6h-3a15 15 0 0 0-1.3-3.9A8 8 0 0 1 18.9 8zM12 4.1A13 13 0 0 1 13.8 8h-3.6A13 13 0 0 1 12 4.1zM4.3 14a8 8 0 0 1 0-4h3.4a16 16 0 0 0 0 4zm.8 2h3a15 15 0 0 0 1.3 3.9A8 8 0 0 1 5.1 16zm3-8h-3a8 8 0 0 1 4.3-3.9A15 15 0 0 0 8.1 8zM12 19.9A13 13 0 0 1 10.2 16h3.6A13 13 0 0 1 12 19.9zm2.3-5.9H9.7a14 14 0 0 1 0-4h4.6a14 14 0 0 1 0 4zm.3 5.9a15 15 0 0 0 1.3-3.9h3a8 8 0 0 1-4.3 3.9zm1.7-5.9a16 16 0 0 0 0-4h3.4a8 8 0 0 1 0 4z"/></svg>www.pinecroftridge.com
      </span>
    </address>
  </section>

  <section class="panel panel--front">
    <div class="panel__frame"></div>
    <div class="brand">
      <span class="brand__mark"></span>
      <span class="brand__name">Pinecroft Ridge</span>
    </div>
    <p class="front-url">www.pinecroftridge.com</p>
  </section>

  <div class="spread__fold"></div>
</main>
</body>
</html>
```